Luxury travel agency needs a website design

We are a travel agency specializing in booking luxury vacations. We specialize in Hawaii, Europe and Caribbean, but will do all vacations. I want a very classy website design which would attract luxury clients. The company name is "Harbors and Hammocks Travel Agency". Would love the web design to go with the color scheme of the logo. Hex codes included in files. Logo is attached. Would also love more Grey in the website. I want it very elegant

Coding

Coded - Design and coding required

Font styles to use
Sans Serif
Decorative

Requirements
Must have
• - Consultation Tab or a page where the client can fill out a short form about what vacation that they would want to book. I want this info to be sent to me in order for me to contact them.
- Somewhere with my contact info "email: marla@harborsandhammockstravel.example and phone number"
- Social media links
- About section "Marla Dunbevy - Agency Owner (picture provided)
Marla has been traveling full time for the passed two years and has been very passionate about travel from a young age. Marla is dedicated to working closely with clients to book their dream vacation.
Marla's specializations include honeymoons and anniversaries focusing on travel in Europe, Hawaii and all inclusive resorts in the Caribbean.

```html
<!DOCTYPE html>
<html lang="en">
<head>
<meta charset="utf-8">
<title>Harbors and Hammocks Travel Agency</title>
<link href="https://fonts.googleapis.com/css2?family=Almendra:wght@400;700&family=Lato:wght@400;700;900&family=Montserrat:ital,wght@0,400;0,600;1,400&display=swap" rel="stylesheet">
<style>
:root{
  --orange:#e8793a;
  --orange-dark:#d96a2c;
  --gold:#f4b63c;
  --ink:#2b2b2b;
  --grey:#555;
  --line:#c9c9c9;
  --soft:#f1f1f1;
  --footer:#2f2f33;
  --white:#fff;
}
*{box-sizing:border-box;margin:0;padding:0}
html,body{width:1200px;height:4485px;overflow:hidden;background:var(--white)}
body{position:relative;font-family:"Lato",sans-serif;color:var(--ink)}
.abs{position:absolute}
.deco{font-family:"Almendra",serif;font-weight:700}

/* hero */
.hero{left:0;top:0;width:1200px;height:779px;background:linear-gradient(180deg,#3f86c9 0%,#6ba6d6 30%,#4d7f6a 55%,#2f5f8a 75%,#8aa0b4 100%)}
.hero-shade{left:0;top:0;width:1200px;height:779px;background:linear-gradient(180deg,rgba(0,0,0,.15),rgba(0,0,0,0) 30%,rgba(0,0,0,.1))}
.social-top{left:75px;top:36px;display:flex;gap:14px}
.dot-icon{width:16px;height:16px;border-radius:50%;background:var(--white)}
.nav{top:92px;height:58px;border-top:1px solid rgba(255,255,255,.8);border-bottom:1px solid rgba(255,255,255,.8);display:flex;align-items:center;justify-content:space-between;font-size:14px;font-weight:700;color:var(--white);letter-spacing:.5px}
.nav-left{left:75px;width:331px}
.nav-right{left:793px;width:332px;justify-content:space-between}
.badge{left:427px;top:0;width:348px;height:183px}
.badge-name{left:427px;top:60px;width:348px;text-align:center;font-family:"Almendra",serif;font-weight:700;font-size:27px;color:var(--ink);line-height:1.1}
.badge-sub{left:427px;top:98px;width:348px;text-align:center;font-family:"Almendra",serif;font-weight:700;font-size:11px;letter-spacing:2px;color:var(--ink)}
.consult{left:988px;top:26px;width:137px;height:38px;background:var(--orange);color:var(--white);font-size:13px;font-weight:700;display:flex;align-items:center;justify-content:center;letter-spacing:.3px}
.hero-title{left:0;top:404px;width:1200px;text-align:center;color:var(--white);font-size:64px;line-height:70px;text-shadow:0 2px 6px rgba(0,0,0,.35)}
.hero-btn{left:514px;top:592px;width:171px;height:40px;background:var(--gold);color:var(--white);font-size:17px;display:flex;align-items:center;justify-content:center}
.dots{left:556px;top:726px;display:flex;gap:10px}
.dots span{width:14px;height:14px;border-radius:50%;background:var(--white)}
.dots span:first-child{background:#222}

/* contact bar */
.contact-bar{left:0;top:779px;width:1200px;height:69px;background:var(--orange);color:var(--white);display:flex;align-items:center;padding:0 75px;font-weight:700;font-size:16px}
.contact-bar .label{font-size:15px;margin-right:20px}
.ci{width:32px;height:32px;border-radius:50%;background:#222;display:flex;align-items:center;justify-content:center;margin-right:14px}
.contact-bar .item{display:flex;align-items:center;margin-right:26px}
.bar-social{margin-left:auto;display:flex;gap:24px}
.bar-social span{width:24px;height:24px;border-radius:50%;background:var(--white)}

/* about */
.portrait{left:75px;top:909px;width:421px;height:441px;background:linear-gradient(135deg,#8a8a80 0%,#6b5f55 40%,#3a7fb0 80%,#5a8a4a 100%)}
.about-box{left:524px;top:949px;width:601px;height:361px;border:2px solid #b9b9b9;padding:26px 27px}
.about-box h2{font-size:38px;line-height:42px;color:var(--ink)}
.about-box .role{font-family:"Montserrat",sans-serif;font-style:italic;color:var(--orange);font-size:24px;margin-top:6px}
.about-box p{font-family:"Montserrat",sans-serif;font-size:14.5px;line-height:26px;color:#444;margin-top:14px}
.btn{background:var(--orange);color:var(--white);font-family:"Almendra",serif;font-weight:700;display:flex;align-items:center;justify-content:center}
.about-btn{width:169px;height:46px;font-size:19px;margin-top:22px}

.divider{left:75px;top:1428px;width:1050px;height:2px;background:var(--line)}
.section-title{left:0;width:1200px;text-align:center;color:var(--ink)}
.spec-title{top:1482px;font-size:34px}

/* destinations */
.tile{width:512px;height:377px;display:flex;align-items:center;justify-content:center;color:var(--white);font-size:60px;text-shadow:0 2px 8px rgba(0,0,0,.4)}
.t-hawaii{left:75px;top:1573px;background:linear-gradient(180deg,#6d8fb4,#2d4f6b 45%,#2f5a3a 75%,#5a7a45);flex-direction:column}
.t-europe{left:613px;top:1573px;background:linear-gradient(180deg,#2f5d93,#4a6f8a 45%,#7a6450 75%,#54604a)}
.t-carib{left:75px;top:1982px;background:linear-gradient(180deg,#b8c4cc,#4d7f9b 45%,#2d5f80 70%,#8a6a4a)}
.t-italy{left:613px;top:1982px;background:linear-gradient(180deg,#c98a9a,#4f6f95 40%,#8a6a50 70%,#2f6a7a)}
.tile-btns{display:flex;gap:28px;margin-top:24px}
.tile-btns span{width:171px;height:46px;border:2px solid var(--gold);color:var(--gold);font-size:19px;display:flex;align-items:center;justify-content:center;text-shadow:none}

/* reviews */
.reviews{left:0;top:2435px;width:1200px;height:457px;background:linear-gradient(90deg,#5a5048,#7a6a5c 40%,#8a7a6a 60%,#4a4540)}
.reviews-shade{left:0;top:2435px;width:1200px;height:457px;background:rgba(30,30,35,.45)}
.rev-title{top:2508px;font-size:38px;color:var(--white)}
.stars{left:0;top:2602px;width:1200px;display:flex;justify-content:center;gap:8px}
.quote{left:130px;top:2640px;width:940px;text-align:center;color:var(--white);font-family:"Montserrat",sans-serif;font-style:italic;font-size:23px;line-height:37px}
.author{left:0;top:2766px;width:1200px;text-align:center;color:var(--white);font-family:"Montserrat",sans-serif;font-weight:600;font-size:24px;letter-spacing:1px}
.arrow{top:2643px}

/* faq */
.faq-title{top:2936px;font-size:40px}
.faq{width:512px;height:52px;border:1px solid #bdbdbd;display:flex;align-items:center;justify-content:space-between;padding:0 16px;font-size:15px;color:#333}
.faq b{font-size:22px;font-weight:900}

/* blog */
.blog-bg{left:0;top:3318px;width:1200px;height:521px;background:linear-gradient(180deg,#e9a866 0%,#d8b89a 25%,#7a9ca8 55%,#2f7f86 75%,#a2583a 100%)}
.blog-card{left:75px;top:3397px;width:512px;height:362px;background:rgba(255,255,255,.88);padding:26px 21px}
.blog-card h2{font-size:40px;line-height:44px}
.blog-card h3{color:var(--orange);font-family:"Montserrat",sans-serif;font-weight:600;font-size:19px;margin-top:12px}
.blog-card .date{font-family:"Montserrat",sans-serif;font-weight:600;font-size:15px;margin-top:6px}
.blog-card p{font-family:"Montserrat",sans-serif;font-size:14.5px;line-height:28px;color:#444;margin-top:8px}
.blog-btn{width:171px;height:45px;font-size:19px;margin-top:18px}

/* newsletter */
.news-title{top:3896px;font-size:40px}
.news-text{left:0;top:3965px;width:1200px;text-align:center;font-size:14px;color:#333}
.news-form{left:314px;top:4013px;width:569px;height:61px;border:2px solid #bdbdbd;display:flex;align-items:center;padding:0 4px 0 15px}
.news-form span{font-size:14px;color:#666;flex:1}
.sub-btn{width:142px;height:47px;font-size:20px}

/* footer */
.footer{left:0;top:4132px;width:1200px;height:293px;background:var(--soft)}
.f-logo{left:75px;top:4268px;width:254px;text-align:center}
.f-logo .nm{font-family:"Almendra",serif;font-weight:700;font-size:27px;color:var(--ink);line-height:1}
.f-logo .tg{font-family:"Almendra",serif;font-weight:700;font-size:10px;letter-spacing:2px;margin-top:4px}
.f-mark{left:188px;top:4212px;width:32px;height:32px;border-radius:50%;background:var(--orange)}
.f-col h4{font-family:"Almendra",serif;font-weight:700;font-size:21px;margin-bottom:6px}
.f-col li{list-style:none;font-size:14.5px;line-height:28.6px;color:#333}
.bottom{left:0;top:4425px;width:1200px;height:60px;background:var(--footer);color:#ddd;display:flex;align-items:center;padding:0 64px;font-size:13px}
.bottom-social{margin-left:auto;display:flex;gap:22px;align-items:center}
.bottom-social span{width:20px;height:20px;border-radius:50%;background:var(--white)}
</style>
</head>
<body>

<header>
  <div class="abs hero" role="img" aria-label="Photo of a couple embracing on a bridge by the river with the Eiffel Tower behind"></div>
  <div class="abs hero-shade"></div>
  <div class="abs social-top"><span class="dot-icon"></span><span class="dot-icon"></span><span class="dot-icon"></span><span class="dot-icon"></span><span class="dot-icon"></span></div>
  <nav class="abs nav nav-left"><span>HOME</span><span>ABOUT</span><span>SERVICES</span></nav>
  <nav class="abs nav nav-right"><span>TOURS</span><span>BLOG</span><span>CONTACT</span></nav>
  <svg class="abs badge" viewBox="0 0 348 183"><path d="M0 0H348V128L174 183L0 128Z" fill="#fff"/></svg>
  <div class="abs badge-name">Harbors &amp; Hammocks</div>
  <div class="abs badge-sub">TRAVEL AGENCY</div>
  <div class="abs consult">CONSULTATION</div>
  <h1 class="abs hero-title deco">Harbors and Hammocks<br>Travel Agency</h1>
  <div class="abs hero-btn deco">Book Your Tours</div>
  <div class="abs dots"><span></span><span></span><span></span><span></span></div>
</header>

<section class="abs contact-bar">
  <span class="label">CONTACT US TODAY</span>
  <span class="item"><span class="ci"><svg width="16" height="16" viewBox="0 0 24 24"><path d="M6.6 10.8a15 15 0 006.6 6.6l2.2-2.2c.3-.3.7-.4 1-.2 1.1.4 2.3.6 3.6.6.6 0 1 .4 1 1V20c0 .6-.4 1-1 1A17 17 0 013 4c0-.6.4-1 1-1h3.5c.6 0 1 .4 1 1 0 1.3.2 2.5.6 3.6.1.3 0 .7-.2 1z" fill="#fff"/></svg></span>1-800-555-0147</span>
  <span class="item"><span class="ci"><svg width="16" height="13" viewBox="0 0 24 18"><path d="M1 1h22v16H1z" fill="#fff"/><path d="M1 1l11 9 11-9" fill="none" stroke="#222" stroke-width="2"/></svg></span>marla@harborsandhammockstravel.example</span>
  <span class="bar-social"><span></span><span></span><span></span><span></span><span></span></span>
</section>

<section>
  <div class="abs portrait" role="img" aria-label="Portrait photo of agency owner Marla Dunbevy"></div>
  <div class="abs about-box">
    <h2 class="deco">About Marla Dunbevy</h2>
    <div class="role">Agency Owner</div>
    <p>Marla has been traveling full time for the passed two years and has been very passionate about travel from a young age. Marla is dedicated to working closely with clients to book their dream vacation. Marla's specializations include honeymoons and anniversaries focusing on travel in Europe, Hawaii and all inclusive resorts in the Caribbean.</p>
    <div class="btn about-btn">Read More</div>
  </div>
</section>

<div class="abs divider"></div>

<section>
  <h2 class="abs section-title spec-title deco">SPECIALIZE IN LUXURY VACATIONS</h2>
  <div class="abs tile t-hawaii deco" role="img" aria-label="Aerial photo of Honolulu coastline at sunset">Hawaii
    <div class="tile-btns"><span>Read More</span><span>Book Tour</span></div>
  </div>
  <div class="abs tile t-europe deco" role="img" aria-label="Aerial photo of a European city along a river">Europe</div>
  <div class="abs tile t-carib deco" role="img" aria-label="Photo of a woman on a swing overlooking the Caribbean sea">Caribbean</div>
  <div class="abs tile t-italy deco" role="img" aria-label="Photo of an Italian cliffside town above the sea">Italy</div>
</section>

<section>
  <div class="abs reviews" role="img" aria-label="Photo of travelers reading a map in a European street"></div>
  <div class="abs reviews-shade"></div>
  <h2 class="abs section-title rev-title deco">Customer Reviews</h2>
  <div class="abs stars">
    <svg width="28" height="27" viewBox="0 0 24 23"><path d="M12 0l3.7 7.5 8.3 1.2-6 5.8 1.4 8.3L12 18.9 4.6 22.8 6 14.5 0 8.7l8.3-1.2z" fill="#f4b63c"/></svg>
    <svg width="28" height="27" viewBox="0 0 24 23"><path d="M12 0l3.7 7.5 8.3 1.2-6 5.8 1.4 8.3L12 18.9 4.6 22.8 6 14.5 0 8.7l8.3-1.2z" fill="#f4b63c"/></svg>
    <svg width="28" height="27" viewBox="0 0 24 23"><path d="M12 0l3.7 7.5 8.3 1.2-6 5.8 1.4 8.3L12 18.9 4.6 22.8 6 14.5 0 8.7l8.3-1.2z" fill="#f4b63c"/></svg>
    <svg width="28" height="27" viewBox="0 0 24 23"><path d="M12 0l3.7 7.5 8.3 1.2-6 5.8 1.4 8.3L12 18.9 4.6 22.8 6 14.5 0 8.7l8.3-1.2z" fill="#f4b63c"/></svg>
    <svg width="28" height="27" viewBox="0 0 24 23"><path d="M12 0l3.7 7.5 8.3 1.2-6 5.8 1.4 8.3L12 18.9 4.6 22.8 6 14.5 0 8.7l8.3-1.2z" fill="#f4b63c"/></svg>
  </div>
  <p class="abs quote">"Sed ut perspiciatis unde omnis iste natus error sit voluptatem accusantium doloremque&nbsp; laudantium, totam rem aperiam, eaque ipsa quae ab illo inventore veritatis et quasi architecto beatae vitae dicta sunt explicabo.."</p>
  <div class="abs author">- Dana Whitcombe</div>
  <svg class="abs arrow" style="left:74px" width="22" height="22" viewBox="0 0 22 22"><path d="M20 11H4M11 3l-8 8 8 8" fill="none" stroke="#fff" stroke-width="3.5"/></svg>
  <svg class="abs arrow" style="left:1106px" width="22" height="22" viewBox="0 0 22 22"><path d="M2 11h16M11 3l8 8-8 8" fill="none" stroke="#fff" stroke-width="3.5"/></svg>
</section>

<section>
  <h2 class="abs section-title faq-title deco">FAQ's</h2>
  <div class="abs faq" style="left:75px;top:3019px"><span>Donec lobortis erat vel erat lobortis accumsan.?</span><b>+</b></div>
  <div class="abs faq" style="left:75px;top:3078px"><span>Donec lobortis erat vel erat lobortis accumsan.?</span><b>+</b></div>
  <div class="abs faq" style="left:75px;top:3137px"><span>Donec lobortis erat vel erat lobortis accumsan.?</span><b>+</b></div>
  <div class="abs faq" style="left:75px;top:3196px"><span>Donec lobortis erat vel erat lobortis accumsan.?</span><b>+</b></div>
  <div class="abs faq" style="left:613px;top:3019px"><span>Donec lobortis erat vel erat lobortis accumsan.?</span><b>+</b></div>
  <div class="abs faq" style="left:613px;top:3078px"><span>Donec lobortis erat vel erat lobortis accumsan.?</span><b>+</b></div>
  <div class="abs faq" style="left:613px;top:3137px"><span>Donec lobortis erat vel erat lobortis accumsan.?</span><b>+</b></div>
  <div class="abs faq" style="left:613px;top:3196px"><span>Donec lobortis erat vel erat lobortis accumsan.?</span><b>+</b></div>
</section>

<section>
  <div class="abs blog-bg" role="img" aria-label="Photo of Venice rooftops and domed basilica at sunset"></div>
  <article class="abs blog-card">
    <h2 class="deco">Blog Posts</h2>
    <h3>Sed ut perspiciatis unde omnis iste natus</h3>
    <div class="date">May18, 2021</div>
    <p>Error sit voluptatem accusantium doloremque. Nemo enim ipsam voluptatem quia voluptas sit aspernatur aut odit aut fugit, sed quia consequuntur magni dolores eos qui ratione voluptatem sequi nesciunt.</p>
    <div class="btn blog-btn">Read More</div>
  </article>
</section>

<section>
  <h2 class="abs section-title news-title deco">Newsletter Sign Up</h2>
  <p class="abs news-text">Sign up with your email address to receive news on our upcoming workshops, travel, and special events.</p>
  <div class="abs news-form"><span>Enter Email Address</span><div class="btn sub-btn">SUBSCRIBE</div></div>
</section>

<footer>
  <div class="abs footer"></div>
  <div class="abs f-mark"></div>
  <div class="abs f-logo"><div class="nm">Harbors &amp; Hammocks</div><div class="tg">TRAVEL AGENCY</div></div>
  <div class="abs f-col" style="left:397px;top:4174px"><h4>Site Map</h4><ul><li>Home</li><li>About</li><li>Services</li><li>Tours</li><li>Blog</li><li>Contact</li></ul></div>
  <div class="abs f-col" style="left:632px;top:4174px"><h4>Tours</h4><ul><li>Sed ut perspiciatis</li><li>Unde omnis iste natus</li><li>Error sit</li><li>Voluptatem</li><li>Accusantium</li><li>Doloremque</li></ul></div>
  <div class="abs f-col" style="left:904px;top:4174px"><h4>Resources</h4><ul><li>Sed ut perspiciatis</li><li>Unde omnis iste natus</li><li>Error sit</li><li>Voluptatem</li><li>Accusantium</li><li>Doloremque</li></ul></div>
  <div class="abs bottom"><span>Copyright © 2021. Company Name. All Right Reserved</span><span class="bottom-social"><span></span><span></span><span></span><span></span><span></span></span></div>
</footer>

</body>
</html>
```